Business Card- Can you make it cool vs boring!

Need a refresh on my business card! Want it to be modern but simple, classic and a pop of coolness! we do senior living and it is boring. but that doesn't mean our business card have to look boring! Open to two sided cards. our website is www.Dunmere-PK.com

Target Market(s)

capital market

Industry/Entity Type

senior housing/ real estate

Contact Information for Business Card

logo/ name/ cell/ address/ www.Dunmere-PK.com/ space for a QR code

Requirements
Must have
• maybe a QR code (do not make prominent I may not use the QR so design where it can be taken out) that link to more about us/ landing page. needs to be modern but clean
Should not have
• clip art or script

```html
<!DOCTYPE html>
<html lang="en">
<head>
<meta charset="utf-8">
<title>Dunmere Park – Business Card</title>
<link rel="stylesheet" href="https://fonts.googleapis.com/css2?family=Poppins:wght@400;500;600&display=swap">
<style>
  :root {
    --page-bg: #e6e1da;
    --card-top: #f6f4f2;
    --card-bottom: #e7e2dd;
    --card-edge: #d3ccc5;
    --maroon: #7a1f12;
    --maroon-band: #8a2a18;
    --band-text: #e9c9bf;
    --ink: #3a3330;
    --muted: #4a4340;
  }
  * { box-sizing: border-box; margin: 0; padding: 0; }
  html, body {
    width: 1200px;
    height: 970px;
    overflow: hidden;
  }
  body {
    background: var(--page-bg);
    font-family: "Poppins", sans-serif;
    position: relative;
  }
  .card {
    position: absolute;
    left: 50px;
    top: 172px;
    width: 1100px;
    height: 625px;
    border-radius: 30px;
    background: linear-gradient(160deg, var(--card-top) 0%, #eeebe8 55%, var(--card-bottom) 100%);
    border: 1px solid var(--card-edge);
    overflow: hidden;
    box-shadow: 0 14px 40px rgba(60, 40, 30, 0.12);
  }
  .brand-name {
    position: absolute;
    left: 60px;
    top: 270px;
    width: 440px;
    text-align: center;
    font-weight: 500;
    font-size: 50px;
    line-height: 1;
    letter-spacing: 0.5px;
    color: var(--maroon);
  }
  .divider {
    position: absolute;
    left: 533px;
    top: 196px;
    width: 2px;
    height: 210px;
    background: var(--muted);
    opacity: 0.7;
  }
  .person {
    position: absolute;
    left: 585px;
    top: 184px;
  }
  .person-name {
    font-weight: 600;
    font-size: 37px;
    line-height: 1.2;
    color: var(--maroon);
  }
  .person-title {
    font-weight: 400;
    font-size: 23px;
    line-height: 1.1;
    color: var(--muted);
  }
  .person-rule {
    width: 84px;
    height: 4px;
    background: var(--maroon);
    margin-top: 20px;
  }
  .contact-list {
    position: absolute;
    left: 585px;
    top: 302px;
    list-style: none;
  }
  .contact-item {
    display: flex;
    align-items: center;
    height: 36.5px;
    font-size: 28px;
    color: var(--ink);
  }
  .contact-icon {
    width: 30px;
    height: 30px;
    margin-right: 18px;
    flex: none;
  }
  .address-band {
    position: absolute;
    left: 0;
    top: 525px;
    width: 100%;
    height: 56px;
    background: linear-gradient(90deg, var(--maroon-band), var(--maroon) 60%, #7e2010);
    display: flex;
    align-items: center;
    justify-content: center;
    font-size: 26px;
    color: var(--band-text);
  }
</style>
</head>
<body>
  <main class="card">
    <div class="brand-name">Dunmere Park</div>

    <div class="divider"></div>

    <div class="person">
      <p class="person-name">Reid T Calloway</p>
      <p class="person-title">CEO</p>
      <div class="person-rule"></div>
    </div>

    <ul class="contact-list">
      <li class="contact-item">
        <svg class="contact-icon" viewBox="0 0 30 30" aria-hidden="true">
          <circle cx="15" cy="15" r="15" fill="#7a1f12"/>
          <path d="M11 8.5c.6-.4 1.3-.2 1.6.4l1.2 2.4c.3.6.1 1.2-.4 1.5l-.9.6c.6 1.6 1.8 3 3.3 3.9l.7-.8c.4-.5 1.1-.6 1.6-.2l2.2 1.5c.5.4.6 1.1.2 1.6l-1 1.2c-.6.7-1.6 1-2.5.7-3.8-1.3-6.6-4.5-7.5-8.4-.2-.9.1-1.8.8-2.3z" fill="#fff"/>
        </svg>
        (555) 204-71860
      </li>
      <li class="contact-item">
        <svg class="contact-icon" viewBox="0 0 30 30" aria-hidden="true">
          <circle cx="15" cy="15" r="15" fill="#7a1f12"/>
          <rect x="8" y="10" width="14" height="10" rx="1.2" fill="none" stroke="#fff" stroke-width="1.6"/>
          <path d="M8.5 10.8 15 15.6l6.5-4.8M8.8 19.3l4.5-4.2M21.2 19.3l-4.5-4.2" fill="none" stroke="#fff" stroke-width="1.4"/>
        </svg>
        hello@dunmerepark.com
      </li>
      <li class="contact-item">
        <svg class="contact-icon" viewBox="0 0 30 30" aria-hidden="true">
          <circle cx="15" cy="15" r="15" fill="#7a1f12"/>
          <g fill="none" stroke="#fff" stroke-width="1.3">
            <circle cx="15" cy="15" r="7"/>
            <ellipse cx="15" cy="15" rx="3" ry="7"/>
            <path d="M8 15h14M9 11.5h12M9 18.5h12"/>
          </g>
        </svg>
        www.Dunmere-PK.com
      </li>
    </ul>

    <div class="address-band">4180 Larkspur Lane, Suite #2107</div>
  </main>
</body>
</html>
```